Ecological Cosmetics (w/ Social Impact) Website

Dr. Wendelin Marovitz Naturprodukte KELVORA®, a small family-run ecological cosmetics “start-up” business (has been around since the mid 90s but only now beginning professionalize management), wishes to redesign its web presence, as part of a comprehensive “facelift” that will also encompass at a later stage its corporate identity (e.g. logo…).
We would like to prepare a new trilingual (later 3 additional languages will be added) website (www.kelvora7.at) that is symbiotic with web 2.0 enabled interwoven with a blog, news section, social networks integrated (e.g. preference/like buttons, Facebook), changing images and announcements appearing on first page, online payment services, mobile internet compatibility (e.g. iOS, Android, BlackBerry… thus no use of Flash, no need for a specific app), etc. and all the other significant trends in the e-commerce realm. The website should be easily and quickly accessible, fun to navigate, allow us to update it simply (through a content manager) and so “sexy” that people will want to return to the web, inform themselves of events and news, and hopefully also try our products.
Our company is based in Austria and specializes in the production of organic cosmetics in the mid-upper pricing range. We pride ourselves in offering natural cosmetics (the meaning of “natural” is relative and each person may have a different definition), with no petrochemical preservatives. Some of our products, such as the mineral salts and black mud powder from the Dead Sea cannot be obtained more naturally, unless you actually visit the area, thus retain all their properties. Our products are not medicine but the basic Dead Sea ingredients are used by spas and clinics in the area to treat many different skin, joint and bone affections. Our male and female customers (no distinction made will be made on our new website), primarily as of the ages of 25 to 65, buy KELVORA® because they:
• Care about the exterior and interior well-being
• Wish to look well cared, preserve their skin’s flexibility, natural splendor & properties
• Prefer natural skin care
• Nourish their skin with vital minerals/trace elements, protecting/treating their skin with natural ingredients
• Willing to pay more than average for natural cosmetics, looking for quality,
• Don’t mind spending about 15 minutes per week preparing a mud mask with some hot water.
• Bathe in water enriched with mineral salts
• Know or are surprised to find out that Dead Sea mud is one of the few, if not the only, naturally astringent (tenses the skin) muds in the world
• Help alleviate skin conditions (e.g. psoriasis, dermatitis, acne, eczema, pustules, oily skin ...), joint (e.g. rheumatism, arthritis ...) and cardiovascular disease.
Amongst the minerals in many of our products (particularly salt, mud), are sulfur and zinc, two naturally disinfecting and healing minerals, thus their common use in many dermatological drugs. Both salt and mud powder are completely natural, and without chemicals additives, quite important when dealing with sensitive or problematic skin, which reacts allergically to certain types of substances. The KELVORA line blends in both ingredients, enriching them with the highest-quality vitamins, essential oils and exceptional plant oils. Many of the competitors creams today use common ingredients such as petrolatum, paraffin (paraffinum liquidum), mineral oil, among others, which are derived from oil, are cheap ingredients (higher margins!) and clog pores!
To underline that this is not a chimera, there are quite a few researchers/scientists/doctors who have written articles about the benefits of the Dead Sea and its naturally occurring substances. Below are some links to abstracts of research papers, which are helpful in understanding the therapeutic potential of the black mud powder and mineral salt:
http://onlinelibrary.wiley.com/doi/10.1111/j.1365-4362.1995.tb03599.x/abstract
http://onlinelibrary.wiley.com/doi/10.1111/j.1365-4632.2005.02079.x/full
http://onlinelibrary.wiley.com/doi/10.1046/j.1365-4362.1997.00204.x/abstract
http://ard.bmj.com/content/49/2/99.short
http://www.springerlink.com/content/pv46n2p1m9p3k131/
http://onlinelibrary.wiley.com/doi/10.1111/j.1365-4632.2005.02621.x/full
http://journals.lww.com/jclinrheum/Abstract/2002/08000/Therapy_With_Mud_Compresses_for_Knee.3.aspx
http://onlinelibrary.wiley.com/doi/10.1111/j.1468-3083.1997.tb00509.x/abstract
http://onlinelibrary.wiley.com/doi/10.1046/j.1529-8019.2003.01622.x/full
http://onlinelibrary.wiley.com/doi/10.1046/j.1365-4362.1999.00583.x/full
The following links lead you to KELVORA® product data, mineral characteristics and a video of how to prepare a facial mud mask:
http://www.kelvora7.at/descargaanalisis.htm
http://www.kelvora7.at/estudio.htm
http://www.clipverse.example/watch?v=Qm4TzLp8WxR
We would like to convey, through our striking and attractive new graphic design, our values to potential clients: quality, 100% natural product, effectiveness, seriousness, confidence, respect for the environment, people, animals (the products are not tested on animals), all of which has a price (they are not cheap!). To put our money where our mouth is and contribute to transforming our planet into a better place, we are discussing with NGOs donating a percentage of certain product sales to support their causes.
Our web currently is available in 3 languages: German, Spanish and English, however, we plan to expand it by another 2 to 3 languages (Portuguese, Russian, Chinese). We are looking for a graphic design that will communicate our values and captivate people's attention, thereby helping us increase sales, projecting a solid and elegant image of reliability, effectiveness, simplicity and trust. Although we are not, and do not wish to, market our products as medicine, we do want to express, through our new graphic design, the fact that these products can be used to treat all types of skin, mitigate certain skin affections (e.g. psoriasis, dermatitis, acne, eczema, sensitive skin), and, depending on each organism’s reaction, different ailments (e.g. arthritis, rheumatism), although they won’t cure them (they can alleviate!).
To get an idea of our company, I invite you to explore our website, www.kelvora7.at, and see photos of our products. Attached please find some photos of our products, including the newly designed black mud powder box. We would like to create a unified corporate image. At this point we know that some, if not all, packages do not convey quality nor our values – this is something we wish to gradually change as each products’ graphic design and packaging gets renewed, consistent with the new brand image. This is work-in-progress and will be addressed as the company grows and has the financial capacity to invest in new design and packaging. We are advancing step by step.
Content-wise, we would provide you with product photos, and the texts to be inserted, but would like to complement these with other photos (e.g. from photobanks that include images of the Dead Sea, beaches, plants, nature…). The design should quickly associate the Internet user/visitor of our website with our values and the idea of quality products. A content manager will be used to update and modify our product portfolio.
Although some people will find us by typing into their web browser the address of our website, many will use search engines to locate us on the WWW. For this purpose, it would also be important that kelvora7.at’s different webpages can be referenced, searched for keywords and allow analysis of webtraffic (e.g. Google Analytics…).
Two colors are being used in our packages, green Pantone No. 326 and blue Pantone No. 072. We are completely flexible in terms of colors.
We hope you find the project interesting. Any questions, please do not hesitate to contact us. Thank you very much for your time, recommendations and proposals. Ideally we can close this project in about 14 days.
Information to be considered and/or included in the design:
• The web will feature an e-commerce shop, whose design should also be included in your creative proposal.
• Cosmetics tend to be divided along the lines of skin types, yet as the KELVORA line is still quite small, we have decided to divide it along treatment areas: hair, face, body. Each product is indicated for a particular skin type.
• Keyword Search box for the entire website
The current web is slow, all in Flash, difficult to navigate, has too many intermediate stages, does not offer a keyword search function, nor incorporate any web 2.0 features. Furthermore, it is more difficult to find and index in search engines as none of the pages have specific web addresses. In terms of intermediate pages, these should be eliminated shortening the time the user needs to obtain the desired information (e.g. the landing page where you choose sex & language, followed by drop of water being filled up), such that the visitor is directly lead to the main page (equal to the landing page). At first glance, the blue background and the drop of water filling up may lead the visitor to believe we are dedicated to something with water, perhaps even plumbing or purification services – such an impression must be avoided. Perhaps one of the ways to analyze all the aspects to be incorporated is an evaluation of our current web’s weaknesses and prepare a design where those are all addressed.
Target Market(s)
Male & female customers, approx. age 18-65, who care about their exterior and interior well being, “worried” about their skin, willing to pay more tha
Industry/Entity Type
Graphic Design
Requirements
Must have
- • The web will also feature a blog and an e-commerce shop, whose designs should also be included in your creative proposal.
• Address current and future languages
Content-wise, we will product photos, and the texts to be inserted, but would like to complement these with other photos (e.g. from photobanks that include images of the Dead Sea, beaches, plants, nature…). The design should quickly associate the Internet user/visitor of our website with our values and the idea of quality products. A content manager will be used to update and modify our product portfolio, as well as effects announcements on the landing page.

```html
<!DOCTYPE html>
<html lang="en">
<head>
<meta charset="utf-8">
<title>KELVORA® Naturprodukte – Home</title>
<link href="https://fonts.googleapis.com/css2?family=Didact+Gothic&family=Open+Sans:ital,wght@1,400&family=PT+Sans:wght@400;700&family=Roboto+Condensed:wght@400;700&display=swap" rel="stylesheet">
<style>
:root{
  --cyan:#4ec0d3;
  --cyan-bright:#5bc8d8;
  --navy:#2b3b7e;
  --heading:#44528a;
  --ink:#1f1f1f;
  --muted:#7a7a7a;
  --line:#dcdfe3;
  --band:#eef8fc;
  --green:#8cc63f;
}
*{margin:0;padding:0;box-sizing:border-box}
html,body{width:874px;height:1200px;overflow:hidden;background:#fff}
body{position:relative;font-family:"PT Sans",sans-serif;color:var(--ink)}
.abs{position:absolute}

.lang{top:11px;left:796px;font:12px "Roboto Condensed",sans-serif;color:#333}
.lang b{font-weight:700;color:#000}
.search{top:36px;left:680px;width:172px;height:19px;border:1px solid #bbb;border-radius:10px;
  font:10px "PT Sans",sans-serif;color:#555;padding:2px 10px;box-shadow:inset 0 1px 2px rgba(0,0,0,.12)}
.search svg{position:absolute;right:6px;top:3px}
.brand-dot{top:52px;left:30px;width:20px;height:20px;border-radius:50%;background:var(--green)}
.nav{top:74px;left:0;width:874px;font:12px "Roboto Condensed",sans-serif;color:var(--cyan);text-transform:uppercase}
.nav span{position:absolute;top:0}

.hero{top:98px;left:10px;width:855px;height:341px;border:1px solid var(--line);box-shadow:0 1px 3px rgba(0,0,0,.1);background:#fff;overflow:hidden}
.hero-photo{position:absolute;left:385px;top:8px;width:446px;height:326px;
  background:linear-gradient(90deg,#fff 0%,#f4f2f0 30%,#efe4dc 55%,#e8d3c4 75%,#f1ece8 100%)}
.hero-mark{position:absolute;left:213px;top:64px;width:84px;height:84px;border-radius:50%;background:var(--navy)}
.hero-name{position:absolute;left:150px;top:158px;width:210px;text-align:center;font:700 22px/26px "PT Sans",sans-serif;color:var(--navy)}
.hero-tagline{position:absolute;left:25px;top:230px;width:500px;font:15px/20px "PT Sans",sans-serif;color:var(--navy)}

.category-band{top:455px;left:10px;width:855px;height:157px;background:var(--band)}
.tabs{top:463px;left:25px;font:10.5px "Roboto Condensed",sans-serif;color:#222;text-transform:uppercase}
.tab{position:absolute;top:0;height:25px;line-height:28px;white-space:nowrap}
.tab.active{left:0;width:73px;background:#fff;border:1px solid var(--line);border-bottom:none;text-align:center;color:var(--cyan);z-index:2}
.panel{top:487px;left:22px;width:813px;height:113px;background:#fff;border:1px solid var(--line)}
.product{position:absolute;top:14px;width:260px}
.product-photo{position:absolute;left:0;top:0;width:88px;height:88px;border-radius:50%;
  background:radial-gradient(circle at 50% 30%,#5ab3b3 0%,#2e8a8f 45%,#b9c9d2 60%,#dfe6ec 100%);box-shadow:2px 3px 4px rgba(0,0,0,.15)}
.product h3{position:absolute;left:101px;top:28px;font:400 11px "Didact Gothic",sans-serif;color:var(--navy);letter-spacing:.3px}
.product p{position:absolute;left:101px;top:50px;width:150px;font:700 9px/12px "PT Sans",sans-serif;color:var(--navy);hyphens:auto}

h2.section{font:400 22px "Didact Gothic",sans-serif;color:var(--heading);letter-spacing:.5px}
.welcome-title{top:632px;left:29px}
.welcome-text{top:669px;left:28px;width:585px;font:10px/15.3px "PT Sans",sans-serif;text-align:justify}
.welcome-text p{margin-bottom:15.3px}
.photos-title{top:838px;left:24px}
.tile{position:absolute;width:79px;height:82px}
.tile span{position:absolute;left:2px;bottom:6px;transform-origin:left bottom;transform:rotate(-90deg) translate(0,14px);
  font:11px "PT Sans",sans-serif;color:#fff;white-space:nowrap}
.t-sea{background:linear-gradient(160deg,#6fa5d0,#c6b49a 60%,#8b6a4e)}
.t-min{background:linear-gradient(180deg,#8b6a4a,#c4a17a 55%,#6b4b30)}
.t-vit{background:linear-gradient(160deg,#4c7a2f,#d8d3cc 55%,#7a5b3f)}
.t-face{background:linear-gradient(160deg,#b8a188,#e6ddd0 50%,#9b8f6c)}
.video{top:877px;left:364px;width:250px;height:169px;background:#1a1a1a;border-radius:6px;box-shadow:0 2px 4px rgba(0,0,0,.3)}
.video-frame{position:absolute;left:7px;top:8px;width:236px;height:143px;background:linear-gradient(135deg,#6b4030,#c98f6a 45%,#e8c3a5 70%,#8a5a42)}
.video svg{position:absolute}

.news-title{top:621px;left:643px;font:italic 15px "Open Sans",sans-serif;color:var(--cyan)}
.news-item{position:absolute;left:648px;width:186px;height:50px}
.news-item svg{position:absolute;left:0;top:0}
.news-item p{position:absolute;left:47px;top:0;width:137px;font:10.5px/15.5px "PT Sans",sans-serif;text-align:justify;color:#222}
.testi-title{top:886px;left:644px;font:italic 15px "Open Sans",sans-serif;color:var(--cyan)}
.testi-photo{top:926px;left:645px;width:64px;height:43px;background:linear-gradient(135deg,#c9b39d,#e9d8c6 50%,#b59a80)}
.testi-quote{top:922px;left:716px;width:116px;font:10.5px/15.5px "PT Sans",sans-serif;text-align:justify;color:#222;hyphens:auto}
.testi-author{top:1022px;left:780px;width:50px;text-align:right;font:700 9px "PT Sans",sans-serif;color:var(--navy)}

.box{border:1px solid var(--line);background:#fff;box-shadow:0 1px 2px rgba(0,0,0,.08)}
.box-inner{position:absolute;left:4px;top:4px;right:4px;bottom:4px;background:var(--cyan-bright)}
.follow{top:1063px;left:22px;width:242px;height:62px}
.follow-label{position:absolute;left:27px;top:19px;font:15px "PT Sans",sans-serif;color:#fff}
.social{position:absolute;top:9px;width:34px;height:35px;background:#fff;border-radius:5px}
.newsletter{top:1063px;left:271px;width:574px;height:62px}
.newsletter-label{position:absolute;left:22px;top:18px;font:15px "PT Sans",sans-serif;color:#fff}
.newsletter-input{position:absolute;left:206px;top:14px;width:235px;height:24px;background:#fff;border:1px solid #d6e9ee}
.subscribe{position:absolute;left:454px;top:13px;width:79px;height:25px;border-radius:12px;
  background:linear-gradient(#fff,#e4e4e4);border:1px solid #999;font:15px "PT Sans",sans-serif;color:#111;text-align:center;line-height:23px}

.footer{top:1151px;left:0;width:874px;text-align:center;font:8px/16px "PT Sans",sans-serif;color:var(--muted)}
</style>
</head>
<body>

<div class="abs lang"><b>EN</b> | DE | ES</div>
<div class="abs search">Search
  <svg width="14" height="12" viewBox="0 0 14 12"><circle cx="5" cy="5" r="3.8" fill="none" stroke="#bbb" stroke-width="1.4"/><line x1="8" y1="8" x2="12.5" y2="11" stroke="#bbb" stroke-width="1.6"/></svg>
</div>

<div class="abs brand-dot"></div>
<nav class="abs nav">
  <span style="left:28px">Home</span>
  <span style="left:107px">Kelvora</span>
  <span style="left:191px">Dead Sea</span>
  <span style="left:287px">Aromatherapy</span>
  <span style="left:413px">Facial Care</span>
  <span style="left:523px">Body Care</span>
  <span style="left:626px">Hair Care</span>
  <span style="left:726px">Spas</span>
  <span style="left:801px">Contact</span>
</nav>

<section class="abs hero">
  <div class="hero-photo" role="img" aria-label="Photo of a relaxed spa guest with a towel wrap holding a white calla lily"></div>
  <div class="hero-mark"></div>
  <div class="hero-name">KELVORA®</div>
  <p class="hero-tagline">Lorem ipsum dolor sit amet, consectetur adipiscing elit. Etiam vel rutrum elit. Duis elit quam, eleifend eget sollicitudin sed, sodales vitae tortor.</p>
</section>

<div class="abs category-band"></div>
<div class="abs tabs">
  <div class="tab active">Dead Sea</div>
  <div class="tab" style="left:99px">Aromatherapy</div>
  <div class="tab" style="left:206px">Facial Care</div>
  <div class="tab" style="left:300px">Body Care</div>
  <div class="tab" style="left:389px">Hair Care</div>
  <div class="tab" style="left:474px">Spas</div>
</div>
<div class="abs panel">
  <div class="product" style="left:9px">
    <div class="product-photo" role="img" aria-label="Product photo of Dead Sea mineral bath salt in a jar"></div>
    <h3>LOREM IPSUM</h3>
    <p>dolor sit amet, consectetur adipiscing elit. Etiam vel rutrum elit.</p>
  </div>
  <div class="product" style="left:262px">
    <div class="product-photo" role="img" aria-label="Product photo of Dead Sea mineral bath salt in a jar"></div>
    <h3>LOREM IPSUM</h3>
    <p>dolor sit amet, consectetur adipiscing elit. Etiam vel rutrum elit.</p>
  </div>
  <div class="product" style="left:535px">
    <div class="product-photo" role="img" aria-label="Product photo of Dead Sea mineral bath salt in a jar"></div>
    <h3>LOREM IPSUM</h3>
    <p>dolor sit amet, consectetur adipiscing elit. Etiam vel rutrum elit.</p>
  </div>
</div>

<h2 class="abs section welcome-title">WELCOME</h2>
<div class="abs welcome-text">
  <p>Lorem ipsum dolor sit amet, consectetur adipiscing elit. Etiam vel rutrum elit. Duis elit quam, eleifend eget sollicitudin sed, sodales vitae tortor. Aenean venenatis, dui eget rutrum elementum, ipsum quam mollis libero, nec molestie nulla diam eu neque. Duis vestibulum massa sit amet nunc hendrerit feugiat ac sed diam.</p>
  <p>Proin nibh justo, fermentum vel tristique vitae, placerat ut leo. Quisque sodales bibendum risus ac vulputate. Praesent nisi dui, tincidunt luctus pulvinar id, sodales sit amet orci.</p>
  <p>Aenean id consequat tellus. Nulla posuere vehicula lacinia. Donec sit amet erat quam. Ut pellentesque, ante faucibus adipiscing iaculis, mi justo facilisis elit, vel placerat magna erat nec magna. Vestibulum eget est ligula. Cras et commodo nibh. Morbi nulla odio, porta a tincidunt in, faucibus a felis. Vestibulum lobortis tincidunt pretium. Etiam turpis dolor, condimentum ac tempor sit amet, ornare ac leo.</p>
</div>

<h2 class="abs section photos-title">PHOTO SHARING</h2>
<div class="tile t-sea" style="left:24px;top:876px" role="img" aria-label="Photo of a mud mask at the Dead Sea shore"><span>Dead Sea</span></div>
<div class="tile t-min" style="left:107px;top:876px" role="img" aria-label="Photo of hands pouring minerals"><span>Minerals</span></div>
<div class="tile t-vit" style="left:191px;top:876px" role="img" aria-label="Photo of bath salt in a wooden bowl with herbs"><span>Vitamins</span></div>
<div class="tile t-face" style="left:275px;top:876px" role="img" aria-label="Photo of a facial mask treatment"><span>Face Care</span></div>
<div class="tile t-sea" style="left:22px;top:966px" role="img" aria-label="Photo of a mud mask at the Dead Sea shore"><span>Dead Sea</span></div>
<div class="tile t-min" style="left:106px;top:966px" role="img" aria-label="Photo of hands pouring minerals"><span>Minerals</span></div>
<div class="tile t-vit" style="left:190px;top:966px" role="img" aria-label="Photo of bath salt in a wooden bowl with herbs"><span>Vitamins</span></div>
<div class="tile t-face" style="left:274px;top:966px" role="img" aria-label="Photo of a facial mask treatment"><span>Face Care</span></div>

<div class="abs video">
  <div class="video-frame" role="img" aria-label="Video still of a relaxing back massage"></div>
  <svg style="left:105px;top:60px" width="30" height="30" viewBox="0 0 30 30"><circle cx="15" cy="15" r="14" fill="rgba(40,40,40,.75)"/><path d="M11 8 L22 15 L11 22Z" fill="#7ac143"/></svg>
  <svg style="left:6px;top:154px" width="238" height="10" viewBox="0 0 238 10"><rect x="0" y="4" width="205" height="2" fill="#444"/><rect x="0" y="4" width="20" height="2" fill="#7ac143"/><path d="M212 2 L218 5 L212 8Z" fill="#7ac143"/><rect x="224" y="2" width="2" height="6" fill="#7ac143"/><rect x="228" y="2" width="2" height="6" fill="#7ac143"/></svg>
</div>

<h3 class="abs news-title">News</h3>
<div class="news-item" style="top:652px">
  <svg width="33" height="36" viewBox="0 0 33 36"><rect x=".5" y="3" width="32" height="32" rx="2" fill="#f2f2f2" stroke="#bbb"/><rect x=".5" y="3" width="32" height="11" rx="2" fill="#b3222a"/><rect x="7" y="0" width="3" height="7" rx="1" fill="#666"/><rect x="23" y="0" width="3" height="7" rx="1" fill="#666"/><text x="16.5" y="31" text-anchor="middle" font-family="PT Sans, sans-serif" font-weight="700" font-size="16" fill="#222">22</text></svg>
  <p>Lorem ipsum dolor sit amet, consectetur adipiscing elit. Etiam vel rutrum elit.</p>
</div>
<div class="news-item" style="top:708px">
  <svg width="33" height="36" viewBox="0 0 33 36"><rect x=".5" y="3" width="32" height="32" rx="2" fill="#f2f2f2" stroke="#bbb"/><rect x=".5" y="3" width="32" height="11" rx="2" fill="#b3222a"/><rect x="7" y="0" width="3" height="7" rx="1" fill="#666"/><rect x="23" y="0" width="3" height="7" rx="1" fill="#666"/><text x="16.5" y="31" text-anchor="middle" font-family="PT Sans, sans-serif" font-weight="700" font-size="16" fill="#222">22</text></svg>
  <p>Lorem ipsum dolor sit amet, consectetur adipiscing elit. Etiam vel rutrum elit.</p>
</div>
<div class="news-item" style="top:764px">
  <svg width="33" height="36" viewBox="0 0 33 36"><rect x=".5" y="3" width="32" height="32" rx="2" fill="#f2f2f2" stroke="#bbb"/><rect x=".5" y="3" width="32" height="11" rx="2" fill="#b3222a"/><rect x="7" y="0" width="3" height="7" rx="1" fill="#666"/><rect x="23" y="0" width="3" height="7" rx="1" fill="#666"/><text x="16.5" y="31" text-anchor="middle" font-family="PT Sans, sans-serif" font-weight="700" font-size="16" fill="#222">22</text></svg>
  <p>Lorem ipsum dolor sit amet, consectetur adipiscing elit. Etiam vel rutrum elit.</p>
</div>
<div class="news-item" style="top:824px">
  <svg width="33" height="36" viewBox="0 0 33 36"><rect x=".5" y="3" width="32" height="32" rx="2" fill="#f2f2f2" stroke="#bbb"/><rect x=".5" y="3" width="32" height="11" rx="2" fill="#b3222a"/><rect x="7" y="0" width="3" height="7" rx="1" fill="#666"/><rect x="23" y="0" width="3" height="7" rx="1" fill="#666"/><text x="16.5" y="31" text-anchor="middle" font-family="PT Sans, sans-serif" font-weight="700" font-size="16" fill="#222">22</text></svg>
  <p>Lorem ipsum dolor sit amet, consectetur adipiscing elit. Etiam vel rutrum elit.</p>
</div>

<h3 class="abs testi-title">Testimtonials</h3>
<div class="abs testi-photo" role="img" aria-label="Photo of two smiling customers"></div>
<p class="abs testi-quote">“Lorem ipsum dolor sit amet, consectetur adipiscing elit. Etiam vel rutrum elit. Duis elit quam, eleifend eget sollicitudin sed, sodales vitae tortor.”</p>
<p class="abs testi-author">- Zone</p>

<div class="abs box follow">
  <div class="box-inner">
    <span class="follow-label">follow us on</span>
    <span class="social" style="left:120px"></span>
    <span class="social" style="left:164px"></span>
  </div>
</div>
<div class="abs box newsletter">
  <div class="box-inner">
    <span class="newsletter-label">Subscribe your Newsletter</span>
    <span class="newsletter-input"></span>
    <span class="subscribe">Subscribe</span>
  </div>
</div>

<footer class="abs footer">
  Copyright ©2012 by KELVORA NATURPRODUKTE DR. WENDELIN MAROVITZ. All rights reserved.<br>
  www.kelvora7.at &nbsp; Email: info@kelvora7.at<br>
  Visit KELVORA® and learn more about the skin
</footer>

</body>
</html>
```